New Business card design to reflect rebrand

I would like a business card design with a good base colour for our new logo and also a placeholder for a profile pic of the card holder. the design needs to be editable to the point that we can easily change the picture of the person and use that design for printmerlo etc. we are looking at a metalic finish business card so will need a good base colour to bring out the finish.

Target Market(s)

prospective customers

Industry/Entity Type

Business

Contact Information for Business Card

I would like one editable design that we can change the name of the card holder and profile picture. The design need to be in a format that be send to printmerlo etc.

Our address is Fenwick Lodge, Copse Lane, Hartley Wintney, GU14 3TP Tel no. 01483 556172

Requirements
Must have
• place holder for a profile pic for the card holder. in AI or preferably PSD format

```html
<!DOCTYPE html>
<html lang="en">
<head>
<meta charset="utf-8">
<title>Corvane Workplace Services – Business Card</title>
<link rel="stylesheet" href="https://fonts.googleapis.com/css2?family=Lato:wght@400;700&display=swap">
<style>
  :root {
    --orange: #e8620b;
    --navy: #3e5572;
    --white: #ffffff;
    --page: #ededed;
    --photo-light: #e9e6e3;
    --photo-dark: #2a2c33;
  }
  * { box-sizing: border-box; margin: 0; padding: 0; }
  html, body { width: 1200px; height: 1200px; overflow: hidden; }
  body {
    background: var(--page);
    font-family: "Lato", Arial, sans-serif;
    position: relative;
  }
  .card {
    position: absolute;
    left: 150px;
    width: 900px;
    height: 514px;
    overflow: hidden;
    box-shadow: 0 10px 30px rgba(0,0,0,.18);
  }
  .card--back { top: 629px; background: var(--orange); }
  .card--front { top: 57px; background: var(--orange); }
  .card__art { position: absolute; inset: 0; }

  /* back */
  .brand {
    position: absolute;
    color: var(--navy);
    font-weight: 700;
    text-align: center;
    line-height: 1;
  }
  .brand__name { display: block; }
  .brand__tag { display: block; }
  .card--back .brand { left: 140px; width: 620px; top: 140px; }
  .card--back .brand__name { font-size: 104px; letter-spacing: 4px; }
  .card--back .brand__tag { font-size: 32px; letter-spacing: 9px; margin-top: 18px; }
  .back__web {
    position: absolute;
    left: 0; width: 900px; top: 426px; height: 56px;
    display: flex; align-items: center; justify-content: center;
    color: var(--white);
    font-size: 25px;
    letter-spacing: 5px;
  }

  /* front */
  .card--front .brand { left: 70px; width: 420px; top: 92px; }
  .card--front .brand__name { font-size: 72px; letter-spacing: 3px; }
  .card--front .brand__tag { font-size: 22px; letter-spacing: 6px; margin-top: 14px; }
  .address {
    position: absolute;
    left: 38px; top: 274px; height: 75px;
    display: flex; align-items: center; gap: 16px;
    color: var(--white);
    font-size: 16px;
  }
  .icon {
    width: 28px; height: 28px; border-radius: 6px;
    display: inline-flex; align-items: center; justify-content: center;
    flex: none;
  }
  .icon--orange { background: var(--orange); }
  .icon--navy { background: var(--navy); }
  .icon svg { width: 18px; height: 18px; }
  .contact {
    position: absolute;
    display: flex; align-items: center; gap: 16px;
    color: var(--white);
    font-size: 21px;
  }
  .photo {
    position: absolute;
    left: 650px; top: 125px; width: 217px; height: 221px;
    border: 4px solid var(--navy);
    border-radius: 10px;
    background: linear-gradient(180deg, var(--photo-light) 0%, var(--photo-light) 55%, var(--photo-dark) 100%);
  }
  .holder {
    position: absolute;
    right: 33px; text-align: right;
    color: var(--white);
  }
  .holder__name { top: 400px; font-size: 29px; font-weight: 700; }
  .holder__title { top: 444px; font-size: 21px; }
</style>
</head>
<body>

<section class="card card--front" aria-label="Business card front">
  <svg class="card__art" viewBox="0 0 900 514" aria-hidden="true">
    <path d="M0 274 H568 L548 330 Q540 349 520 349 H0 Z" fill="var(--navy)"/>
    <path d="M0 0 H705 Q670 0 657 33 L568 274 H0 Z" fill="var(--white)"/>
  </svg>

  <div class="brand">
    <span class="brand__name">CORVANE</span>
    <span class="brand__tag">WORKPLACE SERVICES</span>
  </div>

  <div class="address">
    <span class="icon icon--orange">
      <svg viewBox="0 0 24 24"><path d="M12 2a7 7 0 0 0-7 7c0 5 7 13 7 13s7-8 7-13a7 7 0 0 0-7-7zm0 9.5A2.5 2.5 0 1 1 12 6.5a2.5 2.5 0 0 1 0 5z" fill="#fff"/></svg>
    </span>
    <span>Address: Street No, Nord Avenue, Co,City/State Zipcode</span>
  </div>

  <div class="contact" style="left:38px; top:392px;">
    <span class="icon icon--navy">
      <svg viewBox="0 0 24 24"><rect x="7" y="2.5" width="10" height="19" rx="2" fill="none" stroke="#fff" stroke-width="2"/><circle cx="12" cy="18" r="1" fill="#fff"/></svg>
    </span>
    <span>+ 000 - 000 - 000</span>
  </div>
  <div class="contact" style="left:38px; top:441px;">
    <span class="icon icon--navy">
      <svg viewBox="0 0 24 24"><path d="M6.6 10.8a15 15 0 0 0 6.6 6.6l2.2-2.2a1 1 0 0 1 1-.25 11.4 11.4 0 0 0 3.6.57 1 1 0 0 1 1 1V20a1 1 0 0 1-1 1A17 17 0 0 1 3 4a1 1 0 0 1 1-1h3.5a1 1 0 0 1 1 1c0 1.25.2 2.45.57 3.6a1 1 0 0 1-.25 1z" fill="#fff"/></svg>
    </span>
    <span>+ 000 - 000 - 000</span>
  </div>
  <div class="contact" style="left:280px; top:392px;">
    <span class="icon icon--navy">
      <svg viewBox="0 0 24 24"><rect x="3" y="5.5" width="18" height="13" rx="2" fill="none" stroke="#fff" stroke-width="2"/><path d="M3.5 7l8.5 6 8.5-6" fill="none" stroke="#fff" stroke-width="2"/></svg>
    </span>
    <span>mail@website.com</span>
  </div>
  <div class="contact" style="left:280px; top:441px;">
    <span class="icon icon--navy">
      <svg viewBox="0 0 24 24" fill="none" stroke="#fff" stroke-width="1.8"><circle cx="12" cy="12" r="9"/><ellipse cx="12" cy="12" rx="4" ry="9"/><path d="M3 12h18M5 7h14M5 17h14"/></svg>
    </span>
    <span>www.website.com</span>
  </div>

  <div class="photo" role="img" aria-label="Profile photo of the card holder"></div>

  <div class="holder holder__name">CARD HOLDER NAME</div>
  <div class="holder holder__title">JOB TITLE/POSITION</div>
</section>

<section class="card card--back" aria-label="Business card back">
  <svg class="card__art" viewBox="0 0 900 514" aria-hidden="true">
    <path d="M232 75 H765 Q785 75 778 95 L700 357 Q694 377 672 377 H138 Q118 377 125 357 L203 95 Q209 75 232 75 Z" fill="var(--white)"/>
    <rect x="0" y="426" width="900" height="56" fill="var(--navy)"/>
  </svg>

  <div class="brand">
    <span class="brand__name">CORVANE</span>
    <span class="brand__tag">WORKPLACE SERVICES</span>
  </div>

  <div class="back__web">www.website.com</div>
</section>

</body>
</html>
```